design a construction company business card

Design business card around our logo. Card must have all the typical info: name, title, address, phone, email, business name, etc. Somewhere on the card I would like to see our motto "Built on integrity... Inspired by commitment." Consider adding a splash of bright orange to the card to complement the blues and silvers/grays in the logo. We are open to metallic inks, textures, etc. We would like to see options on both light and dark backgrounds. The font in the logo is Euro Technic Extended Regular.

```html
<!DOCTYPE html>
<html lang="en">
<head>
<meta charset="utf-8">
<title>Halden Builders, Inc. – Business Card</title>
<link rel="stylesheet" href="https://fonts.googleapis.com/css2?family=Open+Sans:ital,wght@0,400;0,600;0,700;1,400&display=swap">
<style>
  :root {
    --backdrop-light: #f2f3f5;
    --backdrop-dark: #c9ccd1;
    --brand-blue: #1f6fc4;
    --brand-blue-deep: #15439a;
    --brand-blue-back: #2a86d3;
    --accent-orange: #ff8a1f;
    --silver: #9aa0a8;
    --ink: #3a3f47;
    --paper: #ffffff;
  }
  * { box-sizing: border-box; margin: 0; padding: 0; }
  html, body { width: 800px; height: 1200px; overflow: hidden; }
  body {
    font-family: "Open Sans", Arial, sans-serif;
    background: radial-gradient(ellipse at 50% 45%, var(--backdrop-light) 0%, var(--backdrop-dark) 100%);
    position: relative;
  }
  .card {
    position: absolute;
    left: 148px;
    width: 504px;
    height: 288px;
    box-shadow: 0 4px 14px rgba(0,0,0,0.22);
    overflow: hidden;
  }
  .card--front { top: 175px; background: var(--paper); }
  .card--back { top: 700px; background: var(--brand-blue-back); }

  .swoosh { position: absolute; inset: 0; width: 100%; height: 100%; }

  .company {
    position: absolute;
    font-weight: 700;
    letter-spacing: 2px;
    text-transform: uppercase;
    display: flex;
    align-items: center;
    gap: 10px;
    white-space: nowrap;
  }
  .company__mark { width: 14px; height: 14px; }
  .card--front .company { left: 40px; top: 78px; font-size: 19px; color: var(--brand-blue-deep); }
  .card--front .company__mark { background: var(--accent-orange); }
  .card--back .company {
    left: 0; right: 0; top: 110px; justify-content: center;
    font-size: 22px; color: var(--paper);
  }
  .card--back .company__mark { background: var(--accent-orange); }

  .motto {
    position: absolute;
    left: 0; right: 0; top: 166px;
    text-align: center;
    font-size: 11.5px;
    font-style: italic;
    color: var(--paper);
    letter-spacing: 0.3px;
  }
  .motto__rule {
    position: absolute;
    left: 222px; top: 152px;
    width: 60px; height: 2px;
    background: var(--accent-orange);
  }

  .person { position: absolute; left: 40px; top: 172px; }
  .person__name { font-size: 18px; font-weight: 700; color: var(--brand-blue-deep); line-height: 22px; }
  .person__title { font-size: 10.5px; color: var(--ink); margin-top: 1px; }

  .contacts {
    position: absolute;
    right: 22px;
    top: 180px;
    list-style: none;
    color: var(--paper);
    font-size: 10.5px;
    line-height: 19px;
    text-align: right;
  }
  .contacts li { display: flex; justify-content: flex-end; align-items: center; gap: 8px; white-space: nowrap; }
  .contacts svg { width: 10px; height: 10px; flex: none; }
</style>
</head>
<body>

<section class="card card--front" aria-label="Front of business card">
  <svg class="swoosh" viewBox="0 0 504 288" preserveAspectRatio="none" aria-hidden="true">
    <defs>
      <linearGradient id="bandBlue" x1="0" y1="1" x2="1" y2="0">
        <stop offset="0" stop-color="#1a4fa8"/>
        <stop offset="1" stop-color="#2a7fd0"/>
      </linearGradient>
    </defs>
    <path d="M0,226 C190,224 340,176 504,66" fill="none" stroke="var(--silver)" stroke-width="7"/>
    <path d="M0,238 C190,236 345,190 504,80" fill="none" stroke="var(--accent-orange)" stroke-width="3"/>
    <path d="M0,244 C190,242 350,198 504,90 L504,288 L0,288 Z" fill="#4f95da"/>
    <path d="M0,252 C195,250 355,208 504,104 L504,288 L0,288 Z" fill="url(#bandBlue)"/>
  </svg>

  <div class="company"><span class="company__mark"></span>Halden Builders, Inc.</div>

  <div class="person">
    <p class="person__name">Daniel Marlow</p>
    <p class="person__title">Managing Member</p>
  </div>

  <ul class="contacts">
    <li>(555) 214-3081
      <svg viewBox="0 0 10 10"><path d="M2 1 L4 1 L4.6 3 L3.5 4 C4 5.3 4.8 6.1 6 6.6 L7 5.5 L9 6.2 L9 8 C5 8.5 1.5 5 2 1 Z" fill="#fff"/></svg></li>
    <li>(555) 214-3092
      <svg viewBox="0 0 10 10"><rect x="2.5" y="0.5" width="5" height="9" rx="1" fill="#fff"/><rect x="3.5" y="1.7" width="3" height="5.5" fill="#2a7fd0"/></svg></li>
    <li>daniel@haldenbuild.com
      <svg viewBox="0 0 10 10"><rect x="0.5" y="2" width="9" height="6" fill="#fff"/><path d="M0.5 2 L5 5.5 L9.5 2" fill="none" stroke="#2a7fd0" stroke-width="0.9"/></svg></li>
    <li>www.haldenbuild.com
      <svg viewBox="0 0 10 10"><circle cx="5" cy="5" r="4.3" fill="none" stroke="#fff" stroke-width="1.2"/><path d="M0.7 5 H9.3 M5 0.7 V9.3" stroke="#fff" stroke-width="0.9"/></svg></li>
    <li>2210 Ridgeline Ave, Fairview, CA 95210
      <svg viewBox="0 0 10 10"><path d="M5 9.5 C2.5 6.5 1.8 5 1.8 3.6 A3.2 3.2 0 0 1 8.2 3.6 C8.2 5 7.5 6.5 5 9.5 Z" fill="#fff"/><circle cx="5" cy="3.6" r="1.2" fill="#2a7fd0"/></svg></li>
  </ul>
</section>

<section class="card card--back" aria-label="Back of business card">
  <div class="company"><span class="company__mark"></span>Halden Builders, Inc.</div>
  <span class="motto__rule"></span>
  <p class="motto">Built on integrity... Inspired by commitment.</p>
</section>

</body>
</html>
```